Professional Single Page Website Design for Tollbrook Advisory

Tollbrook Advisory is a new business consultancy specializing in providing expert services to small businesses, primarily in the brick-and-mortar retail and food service sectors. We offer a range of services including franchise development and launch, due diligence, and construction management.

Currently, we have a basic website set up at www.tollbrookadvisory.example, but we need a professional touch to enhance its design and functionality.

Project Requirements:
- Single Page Design: For now, we need a single page design that effectively showcases who we are, our services, and contact information.
- Future Expansion: The design should be flexible and scalable for future expansion to include additional pages like specific service offerings, about us, and a dedicated contact page.
- Design Aesthetic: We are looking for a modern yet professional design that aligns with our brand identity.
- Logo: We have a logo that we like, which was also sourced from Pixel Bazaar. The logo files are attached to this project brief.

Key Sections to Include:
- Hero Section: An engaging introduction to Tollbrook Advisory with a strong visual impact.
- About Us: A brief overview of who we are and our mission.
- Team: Section for the profiles of the two principals.
- Services: A clear and concise presentation of our services, including franchise development, due diligence, and construction management.
- Contact Information: Easy-to-find contact details, including a form for inquiries.
- Call to Action: Encouraging visitors to get in touch with us for consultations or further information.

Design Considerations:
- Ensure the design is responsive and mobile-friendly.
- Include high-quality images and icons that complement our services and industry.
- We do not need development services, this is only a design project.

```html
<!DOCTYPE html>
<html lang="en">
<head>
<meta charset="utf-8">
<title>Tollbrook Advisory</title>
<link href="https://fonts.googleapis.com/css2?family=Poppins:ital,wght@0,400;0,500;0,600;0,700;1,400&display=swap" rel="stylesheet">
<style>
:root{
  --green:#97cbb2;
  --green-dark:#7fbb9f;
  --ink:#111111;
  --text:#333333;
  --muted:#555555;
  --pale:#f0f5f3;
  --field:#333333;
  --white:#ffffff;
}
*{box-sizing:border-box;margin:0;padding:0}
html,body{width:1200px;height:4491px;overflow:hidden}
body{font-family:'Poppins',sans-serif;color:var(--text);background:var(--white);position:relative}
.abs{position:absolute}
a{color:inherit;text-decoration:none}

/* header */
.topbar{left:357px;top:0;width:733px;height:30px;background:var(--green);display:flex;align-items:center;font-size:11.5px;color:var(--ink);white-space:nowrap;overflow:hidden}
.topbar .item{display:flex;align-items:center;gap:6px;margin-left:40px;flex:none}
.topbar .item.mail{margin-left:26px}
.topbar .sep{width:1px;height:16px;background:var(--ink);margin-left:24px;flex:none}
.topbar .phone{margin-left:auto;background:var(--ink);color:#fff;height:30px;padding:0 24px;display:flex;align-items:center;gap:8px;flex:none}
.brand{left:112px;top:24px;display:flex;align-items:center;gap:10px;font-size:20px;font-weight:600;color:var(--ink);white-space:nowrap}
.brand .mark{width:36px;height:36px;border-radius:50%;background:var(--green)}
.nav{left:608px;top:58px;display:flex;gap:36px;font-size:15px;font-weight:500;color:var(--ink);white-space:nowrap}
.nav-cta{left:938px;top:47px;width:152px;height:44px;background:var(--ink);color:#fff;font-size:13px;font-weight:500;display:flex;align-items:center;justify-content:center}

/* hero */
.hero{left:0;top:106px;width:1200px;height:690px;overflow:hidden}
.hero-photo{position:absolute;inset:0;background:linear-gradient(90deg,#5b5e5a 0%,#6e4a3e 55%,#7a3b2e 80%,#4e4a46 100%)}
.hero-shade{position:absolute;inset:0;background:rgba(0,0,0,.35)}
.hero-curve{position:absolute;left:0;bottom:0}
.hero-title{left:0;top:280px;width:1200px;text-align:center;color:#fff;font-size:44px;font-weight:600;letter-spacing:-.5px}
.hero-sub{left:0;top:355px;width:1200px;text-align:center;color:#fff;font-size:22px;font-style:italic}
.hero-text{left:200px;top:402px;width:800px;text-align:center;color:#fff;font-size:15px;line-height:26px}
.btn{background:var(--green);color:var(--ink);font-size:14px;font-weight:500;display:flex;align-items:center;justify-content:center}
.hero-btn{left:525px;top:523px;width:152px;height:44px}
.dots{left:550px;top:727px;display:flex;gap:14px;align-items:center}
.dots span{width:12px;height:12px;border-radius:50%;border:1.5px solid #888}
.dots .on{width:18px;height:18px;background:#b6cf3c;border-color:#b6cf3c}

/* headings */
.h2{font-size:38px;font-weight:600;color:var(--ink)}
.underline{height:4px;border-radius:3px;background:var(--green)}

/* about */
.about-h{left:84px;top:900px}
.about-line{left:84px;top:955px;width:254px}
.about-text{left:84px;top:980px;width:492px;font-size:15px;line-height:25.8px;text-align:justify}
.mission-h{left:619px;top:906px;font-size:18px;font-weight:600;color:var(--ink)}
.mission-text{left:619px;top:942px;width:494px;font-size:15px;line-height:25.8px;text-align:justify}
.about-photo{left:78px;top:1238px;width:1014px;height:288px;background:linear-gradient(180deg,#a9c6cf 0%,#d8dcd8 45%,#7f9a6a 100%)}

/* team */
.team{left:0;top:1613px;width:1200px;height:947px;background:var(--green)}
.team-h{left:0;top:1692px;width:1200px;text-align:center}
.team-line{left:472px;top:1752px;width:256px;background:var(--ink)}
.card{background:#fff}
.member{width:469px;height:686px;top:1789px}
.member .photo{width:469px;height:380px;background:linear-gradient(180deg,#b9c4cc,#8a8a86)}
.member .photo.b{background:linear-gradient(180deg,#6a5a4c,#3a302a)}
.member .name{position:absolute;left:26px;top:400px;font-size:24px;font-weight:600;color:var(--ink)}
.member .role{position:absolute;left:26px;top:440px;font-size:15px}
.member .icons{position:absolute;right:32px;top:408px;display:flex;flex-direction:column;gap:12px}
.member .bio{position:absolute;left:26px;top:475px;width:418px;font-size:13px;line-height:21.5px;text-align:justify}
.member .more{position:absolute;left:0;width:100%;top:640px;text-align:center;font-size:16px;font-weight:500;color:var(--ink)}
.member .more span{border-bottom:1.5px solid var(--ink)}

/* services */
.services{left:0;top:2560px;width:1200px;height:832px;background:var(--pale)}
.services-h{left:0;top:2625px;width:1200px;text-align:center}
.services-line{left:472px;top:2686px;width:256px}
.svc{width:300px;height:522px;box-shadow:0 6px 14px rgba(0,0,0,.12);overflow:hidden}
.svc .photo{height:244px}
.svc h3{position:absolute;left:14px;font-size:22px;font-weight:600;color:var(--ink);line-height:29px}
.svc h3.tight{font-size:20.5px;white-space:nowrap;letter-spacing:-.3px}
.svc p{position:absolute;left:14px;width:270px;font-size:16px;line-height:26px}
.svc .corner{position:absolute;right:0;bottom:0}

/* contact */
.contact-h{left:0;top:3462px;width:1200px;text-align:center}
.contact-line{left:500px;top:3522px;width:200px}
.contact-text{left:180px;top:3550px;width:840px;text-align:center;font-size:15px;line-height:25px}
.field{left:274px;width:652px;height:42px;background:var(--field);color:#ddd;font-size:13px;padding:14px 20px}
.field.msg{height:125px}
.submit{left:525px;top:3975px;width:152px;height:44px}

/* footer */
.footer{left:0;top:4098px;width:1200px;height:393px;background:var(--ink);color:#fff}
.f-brand{left:180px;top:4245px;display:flex;align-items:center;gap:14px;font-size:28px;font-weight:500;color:#fff;white-space:nowrap}
.f-brand .mark{width:46px;height:46px;border-radius:50%;border:4px solid #fff}
.f-col{color:#fff}
.f-col h4{font-size:18px;font-weight:600;margin-bottom:6px}
.f-col .bar{width:44px;height:2px;background:#fff;margin-bottom:18px}
.f-col li{list-style:none;font-size:12px;line-height:26px}
.f-rule{left:112px;top:4403px;width:976px;height:1px;background:#777}
.copy{left:0;top:4430px;width:1200px;text-align:center;font-size:14px;color:#fff}
</style>
</head>
<body>

<header>
  <div class="abs topbar">
    <span class="item">
      <svg width="13" height="13" viewBox="0 0 24 24"><path d="M12 2a7 7 0 0 0-7 7c0 5 7 13 7 13s7-8 7-13a7 7 0 0 0-7-7zm0 9.5A2.5 2.5 0 1 1 12 6.5a2.5 2.5 0 0 1 0 5z" fill="#111"/></svg>
      214 Harbor View Ln, Tustin, CA 92780</span>
    <span class="sep"></span>
    <span class="item mail">
      <svg width="15" height="12" viewBox="0 0 24 18"><rect x="1" y="1" width="22" height="16" rx="2" fill="none" stroke="#111" stroke-width="2"/><path d="M1 2l11 8 11-8" fill="none" stroke="#111" stroke-width="2"/></svg>
      info@tollbrookadvisory.example</span>
    <span class="phone">
      <svg width="13" height="13" viewBox="0 0 24 24"><path d="M6.6 10.8a15 15 0 0 0 6.6 6.6l2.2-2.2a1 1 0 0 1 1-.25 11 11 0 0 0 3.6.6 1 1 0 0 1 1 1V20a1 1 0 0 1-1 1A17 17 0 0 1 3 4a1 1 0 0 1 1-1h3.5a1 1 0 0 1 1 1c0 1.25.2 2.45.6 3.6a1 1 0 0 1-.25 1z" fill="#fff"/></svg>
      555-010-4821</span>
  </div>
  <div class="abs brand"><span class="mark"></span>Tollbrook Advisory</div>
  <nav class="abs nav"><a>Home</a><a>About Us</a><a>Team</a><a>Services</a></nav>
  <a class="abs nav-cta">Contact Us</a>
</header>

<section class="abs hero">
  <div class="hero-photo" role="img" aria-label="Photo of a modern brick retail building with storefronts and parking lot"></div>
  <div class="hero-shade"></div>
  <svg class="hero-curve" width="1200" height="150" viewBox="0 0 1200 150">
    <path d="M0 40 Q600 200 1200 40 L1200 150 L0 150 Z" fill="#fff"/>
    <path d="M0 40 Q600 200 1200 40" fill="none" stroke="#97cbb2" stroke-width="14"/>
  </svg>
</section>
<h1 class="abs hero-title">Building Success in Southern California</h1>
<p class="abs hero-sub">Expertise at Every Step: From Planning to Execution</p>
<p class="abs hero-text">At Tollbrook, we blend innovative strategies with local market expertise to guide your commercial real estate ventures. Whether you're launching a new restaurant, investing in retail spaces, or expanding a franchise, our dedicated team is here to turn your real estate aspirations into tangible success. Dive into a partnership that grows with you.</p>
<a class="abs btn hero-btn">Get In Touch</a>
<div class="abs dots"><span></span><span></span><span class="on"></span><span></span></div>

<section>
  <h2 class="abs h2 about-h">About Us</h2>
  <div class="abs underline about-line"></div>
  <p class="abs about-text">Welcome to Tollbrook Advisory, your trusted partner in navigating the complexities of the real estate and small business markets. Founded by industry veterans Adrian Velasco and Kevin Park, we specialize in providing comprehensive services tailored to the unique needs of our clients. Whether you're a franchisee, a new restaurant owner, or a commercial real estate investor, our expertise in due diligence, construction management, and investment property evaluation ensures you make informed, strategic decisions.</p>
  <h3 class="abs mission-h">Our Mission</h3>
  <p class="abs mission-text">At Tollbrook Advisory, we are committed to your success. Our approach combines meticulous analysis, strategic insights, and personalized service to help you achieve your business goals. We pride ourselves on our ability to deliver results that exceed expectations, fostering long-term relationships built on trust and excellence.</p>
  <div class="abs about-photo" role="img" aria-label="Aerial photo of a modern commercial building surrounded by trees and parking"></div>
</section>

<section>
  <div class="abs team"></div>
  <h2 class="abs h2 team-h">Team</h2>
  <div class="abs underline team-line"></div>

  <article class="abs card member" style="left:112px">
    <div class="photo" role="img" aria-label="Portrait photo of principal Adrian Velasco on a rooftop"></div>
    <div class="name">Adrian Velasco</div>
    <div class="role">Principal</div>
    <div class="icons">
      <svg width="16" height="16" viewBox="0 0 24 24"><path d="M6.6 10.8a15 15 0 0 0 6.6 6.6l2.2-2.2a1 1 0 0 1 1-.25 11 11 0 0 0 3.6.6 1 1 0 0 1 1 1V20a1 1 0 0 1-1 1A17 17 0 0 1 3 4a1 1 0 0 1 1-1h3.5a1 1 0 0 1 1 1c0 1.250.2 2.450.6 3.6a1 1 0 0 1-.25 1z" fill="#111"/></svg>
      <svg width="18" height="14" viewBox="0 0 24 18"><rect x="0" y="0" width="24" height="18" rx="2" fill="#111"/><path d="M1 2l11 8 11-8" fill="none" stroke="#fff" stroke-width="2"/></svg>
    </div>
    <p class="bio">Adrian Velasco brings almost 20 years of rich experience as a real estate investor and a pivotal role at one of southern California's largest real estate management firms, where he led sales and marketing strategies to elevate property value and investor returns. His vast expertise spans through strategic development and market analysis, making him a cornerstone for Tollbrook Advisory.</p>
    <a class="more"><span>Learn More</span></a>
  </article>

  <article class="abs card member" style="left:619px">
    <div class="photo b" role="img" aria-label="Portrait photo of principal Kevin Park"></div>
    <div class="name">Kevin Park</div>
    <div class="role">Principal</div>
    <div class="icons">
      <svg width="16" height="16" viewBox="0 0 24 24"><path d="M6.6 10.8a15 15 0 0 0 6.6 6.6l2.2-2.2a1 1 0 0 1 1-.25 11 11 0 0 0 3.6.6 1 1 0 0 1 1 1V20a1 1 0 0 1-1 1A17 17 0 0 1 3 4a1 1 0 0 1 1-1h3.5a1 1 0 0 1 1 1c0 1.25.2 2.45.6 3.6a1 1 0 0 1-.25 1z" fill="#111"/></svg>
      <svg width="18" height="14" viewBox="0 0 24 18"><rect x="0" y="0" width="24" height="18" rx="2" fill="#111"/><path d="M1 2l11 8 11-8" fill="none" stroke="#fff" stroke-width="2"/></svg>
    </div>
    <p class="bio">Kevin Park is a seasoned real estate expert with extensive experience in project and construction management, and a licensed real estate agent in California. Fluent in both English and Korean, he specializes in commercial real estate, bringing invaluable expertise to Tollbrook Advisory.</p>
    <a class="more"><span>Learn More</span></a>
  </article>
</section>

<section>
  <div class="abs services"></div>
  <h2 class="abs h2 services-h">Our Services</h2>
  <div class="abs underline services-line"></div>

  <article class="abs card svc" style="left:112px;top:2731px">
    <div class="photo" role="img" aria-label="Photo of a modern dark commercial building at dusk" style="background:linear-gradient(180deg,#8fa2b6,#3c3f45)"></div>
    <h3 style="top:272px">Franchise Development<br>&amp; Launch</h3>
    <p style="top:350px">At Tollbrook Advisory, our Franchise Development &amp; Launch service is designed to transform your successful business into a thriving franchise.</p>
    <svg class="corner" width="72" height="58" viewBox="0 0 72 58"><path d="M72 0 L72 58 L0 58 Z" fill="#97cbb2"/><path d="M38 42h22m-7-7 7 7-7 7" fill="none" stroke="#111" stroke-width="2.2"/></svg>
  </article>

  <article class="abs card svc" style="left:450px;top:2782px">
    <div class="photo" role="img" aria-label="Photo of a large grey warehouse building with green lawn" style="background:linear-gradient(180deg,#b9c6d3 0%,#8d9096 60%,#6f9a4a 100%)"></div>
    <h3 style="top:282px">Due Diligence</h3>
    <p style="top:340px">Conducting thorough due diligence for business and property transactions to identify potential risks and liabilities.</p>
    <svg class="corner" width="72" height="58" viewBox="0 0 72 58"><path d="M72 0 L72 58 L0 58 Z" fill="#97cbb2"/><path d="M38 42h22m-7-7 7 7-7 7" fill="none" stroke="#111" stroke-width="2.2"/></svg>
  </article>

  <article class="abs card svc" style="left:788px;top:2731px">
    <div class="photo" role="img" aria-label="Photo of a team reviewing construction plans on a table" style="background:linear-gradient(180deg,#c9ced4,#7f8c9c)"></div>
    <h3 class="tight" style="top:283px">Construction Management</h3>
    <p style="top:350px">Conducting thorough due diligence for business and property transactions to identify potential risks and liabilities.</p>
    <svg class="corner" width="72" height="58" viewBox="0 0 72 58"><path d="M72 0 L72 58 L0 58 Z" fill="#97cbb2"/><path d="M38 42h22m-7-7 7 7-7 7" fill="none" stroke="#111" stroke-width="2.2"/></svg>
  </article>
</section>

<section>
  <h2 class="abs h2 contact-h">Contact Us</h2>
  <div class="abs underline contact-line"></div>
  <p class="abs contact-text">Feel free to fill out the form provided on this page for a quick and direct message. We value your input and strive to make your experience with us seamless. Looking forward to connecting with you!</p>
  <div class="abs field" style="top:3631px">Full Name</div>
  <div class="abs field" style="top:3690px">E-mail</div>
  <div class="abs field" style="top:3750px">Phone</div>
  <div class="abs field msg" style="top:3809px">Enter Your Message</div>
  <a class="abs btn submit">Submit</a>
</section>

<footer>
  <div class="abs footer"></div>
  <div class="abs f-brand"><span class="mark"></span>Tollbrook Advisory</div>
  <div class="abs f-col" style="left:521px;top:4166px">
    <h4>Quick Links</h4><div class="bar"></div>
    <ul><li>Home</li><li>About Us</li><li>Team</li><li>Services</li><li>Contact Us</li></ul>
  </div>
  <div class="abs f-col" style="left:703px;top:4166px">
    <h4>Links</h4><div class="bar"></div>
    <ul><li>Copyright</li><li>Terms of Use</li><li>Privacy Policy</li><li>Accessibility</li><li>Sitemap</li></ul>
  </div>
  <div class="abs f-col" style="left:874px;top:4166px">
    <h4>Support</h4><div class="bar"></div>
    <ul><li>Team</li><li>About Us</li><li>Careers</li><li>Our Values</li><li>Data Security</li></ul>
  </div>
  <div class="abs f-rule"></div>
  <p class="abs copy">©2024. All rights reserved.</p>
</footer>

</body>
</html>
```